Business Cards for a law firm

Business cards for our law firm. Use our silhoette logo and OAK PARTNERS - check our website (www.oakpartners.example)

Contact Information for Business Card

our silhouette logo, OAK PARTNERS, 800-555-0147, Dorian Pemberton, dorian@oakpartners.example

Requirements
Must have
• our silhouette logo, OAK PARTNERS, 800-555-0147, Dorian Pemberton, dorian@oakpartners.example

```html
<!DOCTYPE html>
<html lang="en">
<head>
<meta charset="utf-8">
<title>Oak Partners – Business Cards</title>
<link rel="stylesheet" href="https://fonts.googleapis.com/css2?family=Cinzel:wght@400;700&family=Questrial&display=swap">
<style>
  :root{
    --page:#e4e8ea;
    --navy:#22336a;
    --navy-deep:#1c2a5c;
    --sky:#3a9ad8;
    --figure:#3b4a7e;
    --white:#ffffff;
  }
  *{margin:0;padding:0;box-sizing:border-box}
  html,body{width:1200px;height:960px;overflow:hidden;background:var(--page)}
  .canvas{position:relative;width:1200px;height:960px}
  .card{position:absolute;left:250px;width:701px;height:401px;overflow:hidden;background:var(--navy)}
  .card-front{top:60px}
  .card-back{top:500px}

  .front-pattern{position:absolute;inset:0;
    background:
      radial-gradient(ellipse 70% 60% at 85% 10%, rgba(58,154,216,.85), rgba(58,154,216,0) 70%),
      linear-gradient(180deg,var(--navy) 0%,var(--navy-deep) 100%);}
  .front-brand{position:absolute;left:548px;top:276px;display:flex;align-items:center;gap:8px;color:var(--white)}
  .front-brand .mark{width:18px;height:18px;background:var(--white)}
  .front-brand .name{font-family:"Questrial",sans-serif;font-size:14px;line-height:12px;letter-spacing:.3px}

  .brand-band{position:absolute;left:0;top:0;width:116px;height:100%;background:var(--white)}
  .band-name{position:absolute;left:34px;top:22px;height:300px;writing-mode:vertical-rl;transform:rotate(180deg);
    font-family:"Questrial",sans-serif;font-size:38px;letter-spacing:1px;color:var(--navy);text-align:left;white-space:nowrap}
  .band-mark{position:absolute;left:40px;top:333px;width:30px;height:30px;background:var(--navy)}

  .partners-figure{position:absolute;left:514px;top:108px;width:187px;height:293px;
    background:linear-gradient(180deg,rgba(59,74,126,.9),rgba(59,74,126,.55))}

  .holder-name{position:absolute;right:29px;top:243px;font-family:"Cinzel",serif;font-weight:700;font-size:30px;
    color:var(--white);letter-spacing:1px;white-space:nowrap}
  .holder-name .surname{font-weight:400}
  .name-block{position:absolute;left:682px;top:251px;width:19px;height:28px;background:var(--white)}

  .contact-list{position:absolute;right:27px;top:306px;list-style:none}
  .contact-list li{display:flex;align-items:center;justify-content:flex-end;gap:12px;height:23px;
    font-family:"Questrial",sans-serif;font-size:18px;letter-spacing:1px;color:var(--white);text-transform:uppercase}
  .contact-list svg{width:14px;height:14px}
</style>
</head>
<body>
<main class="canvas">
  <section class="card card-front" aria-label="Card front">
    <div class="front-pattern" role="img" aria-label="Repeated pattern of the firm's silhouette emblem fading from light blue to navy"></div>
    <div class="front-brand">
      <span class="mark"></span>
      <span class="name">OAK<br>PARTNERS</span>
    </div>
  </section>

  <section class="card card-back" aria-label="Card back">
    <div class="brand-band">
      <div class="band-name">OAK PARTNERS</div>
      <span class="band-mark"></span>
    </div>
    <div class="partners-figure" role="img" aria-label="Faint silhouettes of two partners standing side by side"></div>
    <h1 class="holder-name">Dorian <span class="surname">Pemberton</span></h1>
    <span class="name-block"></span>
    <ul class="contact-list">
      <li>800-555-0147
        <svg viewBox="0 0 24 24" fill="none" stroke="#fff" stroke-width="2.2" stroke-linejoin="round"><path d="M5 3h4l2 5-2.5 1.5a11 11 0 0 0 6 6L16 13l5 2v4a2 2 0 0 1-2 2A16 16 0 0 1 3 5a2 2 0 0 1 2-2z"/></svg>
      </li>
      <li>www.oakpartners.example
        <svg viewBox="0 0 24 24" fill="none" stroke="#fff" stroke-width="2"><circle cx="12" cy="12" r="10"/><path d="M2 12h20M12 2a15 15 0 0 1 0 20M12 2a15 15 0 0 0 0 20"/></svg>
      </li>
      <li>dorian@oakpartners.example
        <svg viewBox="0 0 24 24" fill="none" stroke="#fff" stroke-width="2" stroke-linejoin="round"><rect x="2" y="6" width="20" height="14"/><path d="M2 6l10 8 10-8"/></svg>
      </li>
    </ul>
  </section>
</main>
</body>
</html>
```